Pizza Coupon App Design Project

*******This project will have a guaranteed payout once I see that there is quality work being designed*********

I require the design (no coding) of 4 vertical screens (the screen will not change for horizontal orientation) for Zentrix and Orbalis. The highest res should be used so it can be scaled for older generation phones.

The mobile app will be used to access pizza coupons.

I do not have a specific style or look that I am going for, although I do not want a childish design (e.g. comic sans). The main requirements are for it to be very easy for users to understand and navigate and to be clean and professional.

I am happy if you only produce a design of the main and store selection screens to which I will give feedback before continuing to design the remaining screens.

The selected artist must be flexible in adapting the final design slightly after the contest is completed, during the app development process (maybe a few small modifications over a month or so).
Please do not include any copyrighted images in your deliverables. I must be the sole owner of the graphics once I have paid for them.

I have included attachments which show the process flow and the screen requirements so that will give you the detail you need to design them. I have also included the logo to assist you in your design., *******This project is now guaranteed *********

I have included attachments which show the process flow and the screen requirements so that will give you the detail you need to design them. I have also included the logo to assist you in your design., *******This project will have a guaranteed payout once I see that there is quality work being designed*********

I have included attachments which show the process flow and the screen requirements so that will give you the detail you need to design them. I have also included the logo to assist you in your design.

Reason: Still looking for the perfect design! ******Project is now guaranteed******

******Project is now guaranteed******

Reason: Starting to get some great designs, we are getting much closer! Keep it up.

Target Market(s)

students and 18-30 year olds - People who want cheap meals and people who order pizza online., students and 18-30 year olds - People who want cheap meals and people who order pizza online., students and 18-30 year olds - People who want cheap meals and people who order pizza online.

Industry/Entity Type

Store

Requirements
Must have
• Must have requirements are listed in the attached documents., Must have requirements are listed in the attached documents., Must have requirements are listed in the attached documents.

```html
<!DOCTYPE html>
<html lang="en">
<head>
<meta charset="utf-8">
<title>Pizza Coupons – Store Coupons</title>
<link href="https://fonts.googleapis.com/css2?family=PT+Sans:wght@400;700&family=PT+Sans+Narrow:wght@700&display=swap" rel="stylesheet">
<style>
  :root {
    --page-bg: #ffffff;
    --screen-bg: #f1ede7;
    --ad-band: #6f6f6f;
    --ad-band-dark: #5a5a5a;
    --ad-text: #8e8e8e;
    --ink: #1c1c1c;
    --icon-grey: #4a4a4a;
    --coupon-orange: #f6a443;
    --coupon-orange-light: #fbbd5e;
    --coupon-orange-dark: #e98d2c;
    --coupon-red: #c7452a;
    --coupon-red-dark: #a9351f;
    --coupon-text: #b8421f;
    --price-bg: #cf5a2f;
    --price-text: #f8c889;
    --track: #2f2f2f;
    --thumb: #c9544a;
    --pill-bg: #f4f4f4;
    --pill-edge: #555555;
  }
  * { box-sizing: border-box; margin: 0; padding: 0; }
  html, body {
    width: 1200px; height: 912px; overflow: hidden;
    background: var(--page-bg);
    font-family: "PT Sans", Arial, sans-serif;
  }
  .app-screen {
    position: absolute; left: 310px; top: 21px;
    width: 580px; height: 870px;
    background: var(--screen-bg);
    overflow: hidden;
  }
  .ad-band {
    height: 128px;
    background: linear-gradient(var(--ad-band), var(--ad-band-dark));
    display: flex; align-items: center; justify-content: center;
    font-size: 34px; color: var(--ad-text); letter-spacing: 1px;
  }
  .filter-pill {
    position: absolute; left: 306px; top: 142px;
    width: 224px; height: 42px;
    border: 2px solid var(--pill-edge); border-radius: 10px;
    background: var(--pill-bg);
    display: flex; overflow: hidden;
  }
  .filter-pill .filter-label {
    flex: 1; padding-left: 16px; font-size: 26px; line-height: 38px; color: var(--ink);
  }
  .filter-pill .filter-button {
    width: 62px; background: linear-gradient(#a9a9a9, #7c7c7c);
    display: flex; align-items: center; justify-content: center;
  }
  .scroll-track {
    position: absolute; left: 540px; top: 150px;
    width: 12px; height: 552px; border-radius: 6px;
    background: var(--track);
  }
  .scroll-thumb {
    height: 118px; border-radius: 6px;
    background: linear-gradient(90deg, #a63e36, var(--thumb), #a63e36);
  }
  .settings-button { position: absolute; left: 528px; top: 718px; }
  .back-button { position: absolute; left: 24px; top: 806px; }
  .store-heading {
    position: absolute; left: 20px; top: 170px;
    display: flex; align-items: center; gap: 16px;
    font-size: 34px; color: var(--ink);
  }
  .coupon-list { position: absolute; left: 14px; top: 232px; width: 510px; }
  .coupon-row { display: flex; align-items: center; height: 118px; margin-bottom: 14px; }
  .coupon-icons {
    width: 62px; display: flex; flex-direction: column; align-items: center; gap: 6px;
  }
  .coupon {
    flex: 1; height: 118px; display: flex;
    border-radius: 6px;
    -webkit-mask:
      radial-gradient(circle 3.5px at 0 50%, #0000 95%, #000) 0 0 / 51% 9px repeat-y,
      radial-gradient(circle 3.5px at 100% 50%, #0000 95%, #000) 100% 0 / 51% 9px repeat-y;
    mask:
      radial-gradient(circle 3.5px at 0 50%, #0000 95%, #000) 0 0 / 51% 9px repeat-y,
      radial-gradient(circle 3.5px at 100% 50%, #0000 95%, #000) 100% 0 / 51% 9px repeat-y;
  }
  .coupon-body {
    flex: 1; position: relative;
    background: linear-gradient(var(--coupon-orange-light), var(--coupon-orange) 55%, var(--coupon-orange-dark));
    padding: 22px 14px 0 20px;
  }
  .coupon-body::after, .coupon-stub::after {
    content: ""; position: absolute; inset: 7px;
    border: 1px dashed rgba(160, 60, 20, .35); border-radius: 4px; pointer-events: none;
  }
  .coupon-offer {
    font-family: "PT Sans Narrow", "Arial Narrow", sans-serif;
    font-weight: 700; font-size: 20px; line-height: 22px;
    color: var(--coupon-text); text-transform: uppercase; width: 150px;
  }
  .coupon-price {
    position: absolute; left: 178px; top: 18px;
    width: 120px; height: 40px; border-radius: 6px;
    background: var(--price-bg); box-shadow: inset 0 1px 3px rgba(0,0,0,.35);
    color: var(--price-text); font-size: 24px; font-weight: 700;
    display: flex; align-items: center; justify-content: center; gap: 5px;
  }
  .coupon-price small { font-size: 14px; }
  .coupon-shared {
    position: absolute; left: 166px; top: 74px;
    font-size: 12px; color: #7a3b14;
  }
  .coupon-shared b { font-size: 15px; color: #3a1a08; margin-left: 8px; }
  .coupon-stub {
    width: 118px; position: relative;
    background: linear-gradient(var(--coupon-red), var(--coupon-red-dark));
    display: flex; flex-direction: column; align-items: center; justify-content: center; gap: 4px;
  }
  .coupon-code { font-size: 12px; color: #2a0f06; }
</style>
</head>
<body>
<main class="app-screen">
  <header class="ad-band">Advertising</header>

  <div class="filter-pill">
    <span class="filter-label">Delivery</span>
    <span class="filter-button">
      <svg width="28" height="28" viewBox="0 0 28 28"><ellipse cx="14" cy="6" rx="11" ry="4" fill="#333"/><path d="M3 7 L12 17 V26 L16 23 V17 L25 7 Z" fill="#333"/></svg>
    </span>
  </div>

  <div class="scroll-track"><div class="scroll-thumb"></div></div>

  <div class="store-heading">
    <svg width="52" height="44" viewBox="0 0 52 44" fill="var(--icon-grey)">
      <rect x="4" y="0" width="44" height="6" rx="2"/>
      <path d="M2 8 H50 L48 18 Q44 22 40 18 Q36 22 32 18 Q28 22 24 18 Q20 22 16 18 Q12 22 8 18 Q4 22 2 18 Z"/>
      <rect x="6" y="24" width="40" height="20"/>
    </svg>
    <span class="store-name">STORE 1</span>
  </div>

  <section class="coupon-list">
    <article class="coupon-row">
      <div class="coupon-icons">
        <svg width="32" height="32" viewBox="0 0 32 32" fill="none" stroke="var(--icon-grey)" stroke-width="3"><circle cx="16" cy="16" r="13"/><path d="M16 3 V29 M3 16 H29 M7 7 L25 25 M25 7 L7 25" stroke-width="2"/></svg>
        <svg width="40" height="22" viewBox="0 0 40 22" fill="var(--icon-grey)"><rect x="8" y="2" width="20" height="13"/><path d="M28 6 H34 L38 11 V15 H28 Z"/><circle cx="14" cy="17" r="3.5"/><circle cx="32" cy="17" r="3.5"/><rect x="0" y="5" width="6" height="2"/><rect x="2" y="10" width="5" height="2"/></svg>
      </div>
      <div class="coupon">
        <div class="coupon-body">
          <p class="coupon-offer">What you get for using the coupon</p>
          <div class="coupon-price"><small>AU$</small>5.00</div>
          <p class="coupon-shared">Shared by:<b>example-user</b></p>
        </div>
        <div class="coupon-stub">
          <svg width="80" height="54" viewBox="0 0 80 54"><g fill="none" stroke="#2a0f06" stroke-width="3"><circle cx="8" cy="10" r="5"/><circle cx="8" cy="26" r="5"/><path d="M12 13 L28 22 M12 23 L28 12"/><rect x="32" y="4" width="42" height="44" rx="6" stroke-dasharray="7 5"/></g><text x="53" y="35" text-anchor="middle" font-family="PT Sans, sans-serif" font-weight="700" font-size="22" fill="#2a0f06">%</text></svg>
          <span class="coupon-code">Code: XXXXXX</span>
        </div>
      </div>
    </article>

    <article class="coupon-row">
      <div class="coupon-icons">
        <svg width="32" height="32" viewBox="0 0 32 32" fill="none" stroke="var(--icon-grey)" stroke-width="3"><path d="M4 6 Q18 2 28 10 L10 28 Z"/><circle cx="14" cy="12" r="2" fill="var(--icon-grey)"/><circle cx="12" cy="20" r="2" fill="var(--icon-grey)"/></svg>
        <svg width="40" height="22" viewBox="0 0 40 22" fill="var(--icon-grey)"><rect x="8" y="2" width="20" height="13"/><path d="M28 6 H34 L38 11 V15 H28 Z"/><circle cx="14" cy="17" r="3.5"/><circle cx="32" cy="17" r="3.5"/><rect x="0" y="5" width="6" height="2"/><rect x="2" y="10" width="5" height="2"/></svg>
      </div>
      <div class="coupon">
        <div class="coupon-body">
          <p class="coupon-offer">What you get for using the coupon</p>
          <div class="coupon-price"><small>AU$</small>5.00</div>
          <p class="coupon-shared">Shared by:<b>example-user</b></p>
        </div>
        <div class="coupon-stub">
          <svg width="80" height="54" viewBox="0 0 80 54"><g fill="none" stroke="#2a0f06" stroke-width="3"><circle cx="8" cy="10" r="5"/><circle cx="8" cy="26" r="5"/><path d="M12 13 L28 22 M12 23 L28 12"/><rect x="32" y="4" width="42" height="44" rx="6" stroke-dasharray="7 5"/></g><text x="53" y="35" text-anchor="middle" font-family="PT Sans, sans-serif" font-weight="700" font-size="22" fill="#2a0f06">%</text></svg>
          <span class="coupon-code">Code: XXXXXX</span>
        </div>
      </div>
    </article>

    <article class="coupon-row">
      <div class="coupon-icons">
        <svg width="32" height="32" viewBox="0 0 32 32" fill="none" stroke="var(--icon-grey)" stroke-width="3"><circle cx="16" cy="16" r="13"/><path d="M16 3 V29 M3 16 H29 M7 7 L25 25 M25 7 L7 25" stroke-width="2"/></svg>
        <svg width="40" height="22" viewBox="0 0 40 22" fill="var(--icon-grey)"><rect x="8" y="2" width="20" height="13"/><path d="M28 6 H34 L38 11 V15 H28 Z"/><circle cx="14" cy="17" r="3.5"/><circle cx="32" cy="17" r="3.5"/><rect x="0" y="5" width="6" height="2"/><rect x="2" y="10" width="5" height="2"/></svg>
      </div>
      <div class="coupon">
        <div class="coupon-body">
          <p class="coupon-offer">What you get for using the coupon</p>
          <div class="coupon-price"><small>AU$</small>5.00</div>
          <p class="coupon-shared">Shared by:<b>example-user</b></p>
        </div>
        <div class="coupon-stub">
          <svg width="80" height="54" viewBox="0 0 80 54"><g fill="none" stroke="#2a0f06" stroke-width="3"><circle cx="8" cy="10" r="5"/><circle cx="8" cy="26" r="5"/><path d="M12 13 L28 22 M12 23 L28 12"/><rect x="32" y="4" width="42" height="44" rx="6" stroke-dasharray="7 5"/></g><text x="53" y="35" text-anchor="middle" font-family="PT Sans, sans-serif" font-weight="700" font-size="22" fill="#2a0f06">%</text></svg>
          <span class="coupon-code">Code: XXXXXX</span>
        </div>
      </div>
    </article>

    <article class="coupon-row">
      <div class="coupon-icons">
        <svg width="32" height="32" viewBox="0 0 32 32" fill="none" stroke="var(--icon-grey)" stroke-width="3"><path d="M4 6 Q18 2 28 10 L10 28 Z"/><circle cx="14" cy="12" r="2" fill="var(--icon-grey)"/><circle cx="12" cy="20" r="2" fill="var(--icon-grey)"/></svg>
        <svg width="40" height="22" viewBox="0 0 40 22" fill="var(--icon-grey)"><rect x="8" y="2" width="20" height="13"/><path d="M28 6 H34 L38 11 V15 H28 Z"/><circle cx="14" cy="17" r="3.5"/><circle cx="32" cy="17" r="3.5"/><rect x="0" y="5" width="6" height="2"/><rect x="2" y="10" width="5" height="2"/></svg>
      </div>
      <div class="coupon">
        <div class="coupon-body">
          <p class="coupon-offer">What you get for using the coupon</p>
          <div class="coupon-price"><small>AU$</small>5.00</div>
          <p class="coupon-shared">Shared by:<b>example-user</b></p>
        </div>
        <div class="coupon-stub">
          <svg width="80" height="54" viewBox="0 0 80 54"><g fill="none" stroke="#2a0f06" stroke-width="3"><circle cx="8" cy="10" r="5"/><circle cx="8" cy="26" r="5"/><path d="M12 13 L28 22 M12 23 L28 12"/><rect x="32" y="4" width="42" height="44" rx="6" stroke-dasharray="7 5"/></g><text x="53" y="35" text-anchor="middle" font-family="PT Sans, sans-serif" font-weight="700" font-size="22" fill="#2a0f06">%</text></svg>
          <span class="coupon-code">Code: XXXXXX</span>
        </div>
      </div>
    </article>
  </section>

  <svg class="settings-button" width="38" height="38" viewBox="0 0 38 38" fill="var(--ink)">
    <g transform="translate(19 19)">
      <rect x="-4" y="-18" width="8" height="36" rx="1"/>
      <rect x="-4" y="-18" width="8" height="36" rx="1" transform="rotate(45)"/>
      <rect x="-4" y="-18" width="8" height="36" rx="1" transform="rotate(90)"/>
      <rect x="-4" y="-18" width="8" height="36" rx="1" transform="rotate(135)"/>
      <circle r="13"/>
      <circle r="5.5" fill="var(--screen-bg)"/>
    </g>
  </svg>

  <svg class="back-button" width="56" height="30" viewBox="0 0 56 30" fill="none" stroke="var(--ink)" stroke-width="5" stroke-linecap="round" stroke-linejoin="round">
    <path d="M52 15 H6 M16 4 L5 15 L16 26"/>
  </svg>
</main>
</body>
</html>
```